KORVA needs a beautiful/corp web page

We are a pump an compressor repair facility in Alberta Canada. We love clean looks. white yellows greens blues. main page should involve conola fields, sun shine

Reason: i will be guaranteeing the project keep up the good work

Requirements
Must have
• open conola fields

```html
<!DOCTYPE html>
<html lang="en">
<head>
<meta charset="utf-8">
<title>KORVA Rotating Solutions</title>
<link href="https://fonts.googleapis.com/css2?family=Questrial&family=Arimo:wght@400;700&display=swap" rel="stylesheet">
<style>
:root{
  --yellow:#f2b632;
  --orange:#f5a10f;
  --green:#8cc63f;
  --lime:#a6cf2e;
  --blue:#1b8fc9;
  --ink:#333333;
  --muted:#666666;
  --line:#d6d6d6;
  --panel:#f0efed;
  --footer:#262223;
}
*{box-sizing:border-box;margin:0;padding:0}
html,body{width:1200px;height:2529px;overflow:hidden;background:#fff}
body{position:relative;font-family:"Questrial",sans-serif;color:var(--ink)}
.abs{position:absolute}

/* header */
.site-header{left:0;top:0;width:1200px;height:90px;background:rgba(255,255,255,.93);z-index:2}
.brand{left:100px;top:22px;display:flex;align-items:center;gap:12px}
.brand-mark{width:26px;height:26px;background:var(--orange);border-radius:50%}
.brand-name{font-family:"Arimo",sans-serif;font-weight:700;font-size:38px;color:#1f2d4a;letter-spacing:1px}
.nav{right:85px;top:0;height:90px;display:flex;align-items:center;font-size:14px;font-family:"Arimo",sans-serif}
.nav a{color:#333;text-decoration:none;padding:0 18px;height:90px;line-height:90px;text-transform:uppercase;letter-spacing:.5px}
.nav a.active{background:var(--yellow);color:#fff}
.nav .search{width:32px;height:32px;background:var(--yellow);margin-left:14px;display:flex;align-items:center;justify-content:center}

/* hero */
.hero{left:0;top:0;width:1200px;height:548px;background:linear-gradient(180deg,#3f86d8 0%,#8fbfe9 28%,#e9f1f7 50%,#9fb9d4 60%,#d7cb2d 66%,#e6d21a 80%,#c5b81c 100%)}
.hero-title{left:92px;top:268px}
.hero-title span{display:inline-block;background:rgba(255,255,255,.55);font-size:46px;color:#3a3a3a;padding:2px 14px;letter-spacing:2px;margin-bottom:8px}
.strap{left:0;top:548px;width:1200px;height:42px;display:flex;font-family:"Arimo",sans-serif;font-weight:700;color:#fff}
.strap-label{width:337px;background:var(--blue);font-size:17px;line-height:42px;padding-left:112px;letter-spacing:.5px}
.strap-text{flex:1;background:var(--lime);font-size:16px;line-height:42px;padding-left:30px}

/* features */
.feature{top:680px;width:220px;text-align:center}
.feature-icon{width:112px;height:112px;border-radius:50%;margin:0 auto;display:flex;align-items:center;justify-content:center}
.feature-icon.orange{background:var(--orange)}
.feature-icon.green{background:var(--green)}
.feature h3{font-weight:400;font-size:17px;margin-top:20px;letter-spacing:1px}
.feature h3.orange{color:var(--orange)}
.feature h3.green{color:var(--green)}
.feature p{font-family:"Arimo",sans-serif;font-size:11px;color:var(--muted);line-height:15px;margin-top:18px}

/* section titles */
.section-title{left:90px;width:1020px;display:flex;align-items:center;gap:26px;font-size:25px;letter-spacing:2px;color:#222}
.section-title::before,.section-title::after{content:"";flex:1;height:1px;background:var(--line)}

/* news */
.news-photo{width:149px;height:106px;background:linear-gradient(180deg,#4d8fd6 0%,#bcd7ef 45%,#dccc22 60%,#d6c316 100%)}
.news-tag{position:absolute;left:0;bottom:0;background:var(--blue);color:#fff;font-size:9px;font-family:"Arimo",sans-serif;padding:3px 6px}
.news-icon{width:32px;height:32px;display:flex;align-items:center;justify-content:center}
.news-icon.green{background:var(--green)}
.news-icon.grey{background:#777}
.news-title{font-family:"Arimo",sans-serif;font-size:14px;color:#222}
.news-date{font-family:"Arimo",sans-serif;font-size:10px;color:#888;margin-top:6px}
.news-body{font-family:"Arimo",sans-serif;font-size:11px;color:#555;line-height:14px;width:265px;margin-top:14px}
.read-more{height:20px;font-family:"Arimo",sans-serif;font-weight:700;font-size:11px;color:#fff;text-align:center;line-height:20px}
.read-more.yellow{background:var(--yellow)}
.read-more.grey{background:#777}

/* slogan */
.slogan{left:0;top:1270px;width:1200px;height:158px;background:linear-gradient(180deg,#7da7cf 0%,#c7d7e3 40%,#cfc23a 62%,#a99c2e 100%);text-align:center;color:#fff;font-size:30px;letter-spacing:2px;padding-top:38px;line-height:42px}

/* about */
.about{left:110px;top:1540px;width:980px;text-align:center;font-family:"Arimo",sans-serif;font-size:15px;line-height:21px;color:#444}
.about p+p{margin-top:18px}

/* contact */
.contact-card{left:93px;top:1787px;width:475px;height:287px;background:var(--panel);padding:40px 0 0 78px;font-family:"Arimo",sans-serif}
.contact-card h4{font-size:23px;font-weight:700;color:#333}
.contact-card p{font-size:19px;color:#333;line-height:26px}
.contact-card .addr{margin-top:28px}
.contact-card .mail{color:var(--green)}
.field{left:621px;width:475px;height:39px;border:1px solid #c8c8c8;font-family:"Arimo",sans-serif;font-size:13px;color:#999;padding:10px 20px}
.field.message{height:121px}
.submit{left:970px;top:2096px;width:126px;height:51px;background:var(--yellow);color:#fff;font-family:"Arimo",sans-serif;font-weight:700;font-size:13px;text-align:center;line-height:51px}

/* clients */
.clients{left:93px;top:2242px;width:1012px;height:101px;border:1px solid var(--line);display:flex;align-items:center;justify-content:space-around;font-family:"Arimo",sans-serif;font-size:24px;font-weight:700;color:#666}
.client{display:flex;align-items:center;gap:10px}
.client .dot{width:22px;height:22px;background:#888}
.client.boxed{background:#999;color:#fff;padding:10px 22px}

/* footer */
.site-footer{left:0;top:2405px;width:1200px;height:124px;background:var(--footer);text-align:center;font-family:"Arimo",sans-serif;font-size:13px;color:#999;padding-top:20px;line-height:25px;letter-spacing:.5px}
</style>
</head>
<body>

<div class="abs hero" role="img" aria-label="Open canola field in bright yellow bloom under a blue sky with white clouds"></div>

<header class="abs site-header">
  <div class="abs brand"><span class="brand-mark"></span><span class="brand-name">KORVA</span></div>
  <nav class="abs nav">
    <a class="active" href="#">Home</a><a href="#">Solutions</a><a href="#">Products</a><a href="#">About</a><a href="#">Contact</a>
    <span class="search"><svg width="16" height="16" viewBox="0 0 16 16"><circle cx="6.5" cy="6.5" r="4.5" fill="none" stroke="#fff" stroke-width="2"/><line x1="10" y1="10" x2="14.5" y2="14.5" stroke="#fff" stroke-width="2.4"/></svg></span>
  </nav>
</header>

<h1 class="abs hero-title"><span>We are a pump an compressor</span><br><span>repair facility in Alberta Canada</span></h1>

<div class="abs strap">
  <div class="strap-label">LOREM IPSUM DOLOR</div>
  <div class="strap-text">Lorem ipsum dolor sit amet, consectetur adipisicing elit, sed do eiusmod tempor.</div>
</div>

<!-- features -->
<div class="abs feature" style="left:95px">
  <div class="feature-icon orange"><svg width="60" height="60" viewBox="0 0 60 60" fill="none" stroke="#fff" stroke-width="5"><path d="M22 14 L30 6 L38 18"/><path d="M48 30 L52 42 L38 46"/><path d="M16 46 L8 36 L16 24"/><path d="M40 14 l-2 6 l-6 -2" stroke-width="3"/></svg></div>
  <h3 class="orange">LOREM IPSUM</h3>
  <p>Sed ut perspiciatis unde omnis iste natus error sit voluptatem accusantium dolor emque laudantium</p>
</div>
<div class="abs feature" style="left:359px">
  <div class="feature-icon green"><svg width="60" height="60" viewBox="0 0 60 60" fill="none" stroke="#fff" stroke-width="3"><circle cx="30" cy="30" r="22"/><ellipse cx="30" cy="30" rx="10" ry="22"/><line x1="8" y1="30" x2="52" y2="30"/><line x1="30" y1="8" x2="30" y2="52"/><path d="M12 19 H48 M12 41 H48"/></svg></div>
  <h3 class="green">LOREM IPSUM</h3>
  <p>Sed ut perspiciatis unde omnis iste natus error sit voluptatem accusantium dolor emque laudantium</p>
</div>
<div class="abs feature" style="left:621px">
  <div class="feature-icon orange"><svg width="60" height="60" viewBox="0 0 60 60" fill="none" stroke="#fff" stroke-width="5"><path d="M22 14 L30 6 L38 18"/><path d="M48 30 L52 42 L38 46"/><path d="M16 46 L8 36 L16 24"/><path d="M40 14 l-2 6 l-6 -2" stroke-width="3"/></svg></div>
  <h3 class="orange">LOREM IPSUM</h3>
  <p>Sed ut perspiciatis unde omnis iste natus error sit voluptatem accusantium dolor emque laudantium</p>
</div>
<div class="abs feature" style="left:882px">
  <div class="feature-icon green"><svg width="60" height="60" viewBox="0 0 60 60" fill="none" stroke="#fff" stroke-width="3"><circle cx="30" cy="30" r="22"/><ellipse cx="30" cy="30" rx="10" ry="22"/><line x1="8" y1="30" x2="52" y2="30"/><line x1="30" y1="8" x2="30" y2="52"/><path d="M12 19 H48 M12 41 H48"/></svg></div>
  <h3 class="green">LOREM IPSUM</h3>
  <p>Sed ut perspiciatis unde omnis iste natus error sit voluptatem accusantium dolor emque laudantium</p>
</div>

<!-- news -->
<h2 class="abs section-title" style="top:985px">Latest News</h2>

<div class="abs news-photo" style="left:90px;top:1057px" role="img" aria-label="Canola field under blue sky"><span class="news-tag">0 Comments</span></div>
<div class="abs news-icon green" style="left:267px;top:1057px"><svg width="16" height="16" viewBox="0 0 16 16" fill="none" stroke="#fff" stroke-width="1.6"><rect x="1.5" y="2.5" width="13" height="11"/><path d="M2 12 L6 7 L9 10 L11 8 L14 12"/></svg></div>
<div class="abs" style="left:312px;top:1055px">
  <div class="news-title">Lorem ipsum dolor sit amet</div>
  <div class="news-date">12 OCTOBER 2013</div>
  <div class="news-body">Sed ut perspiciatis unde omnis iste natus error sit voluptatem accusantium doloremque laudantium, totam rem aperiam, eaque ipsa quae ab illo inventore veritatis et</div>
</div>
<div class="abs read-more yellow" style="left:489px;top:1189px;width:96px">Read more</div>

<div class="abs news-photo" style="left:610px;top:1057px" role="img" aria-label="Canola field under blue sky"><span class="news-tag">0 Comments</span></div>
<div class="abs news-icon grey" style="left:787px;top:1057px"><svg width="16" height="16" viewBox="0 0 16 16" fill="none" stroke="#fff" stroke-width="1.8"><path d="M2 14 L4 10 L12 2 L14 4 L6 12 Z"/></svg></div>
<div class="abs" style="left:832px;top:1055px">
  <div class="news-title">Lorem ipsum dolor sit amet</div>
  <div class="news-date">12 OCTOBER 2013</div>
  <div class="news-body">Sed ut perspiciatis unde omnis iste natus error sit voluptatem accusantium doloremque laudantium, totam rem aperiam, eaque ipsa quae ab illo inventore veritatis et</div>
</div>
<div class="abs read-more grey" style="left:995px;top:1189px;width:107px">Read more</div>

<!-- slogan -->
<div class="abs slogan" role="img" aria-label="Blurred canola field with sky, behind slogan text"><span>Your slogan or middle text - lorem ipsum<br>sed ut perspiciatis unde</span></div>

<!-- about -->
<h2 class="abs section-title" style="top:1486px">About us</h2>
<div class="abs about">
  <p>Sed ut perspiciatis unde omnis iste natus error sit voluptatem accusantium doloremque laudantium, totam rem aperiam, eaque ipsa quae ab illo inventore veritatis et.</p>
  <p>Quasi arch sed ut perspiciatis unde omnis iste natus error sit voluptatem accusantium doloremque laudantium, totam rem aperiam, eaque ipsa quae ab illo inventore veritatis et quasi arch.</p>
</div>

<!-- contact -->
<h2 class="abs section-title" style="top:1716px">Get in touch with us</h2>
<div class="abs contact-card">
  <h4>KORVA Rotating Solutions</h4>
  <p class="addr">111 Address, City, State 0000</p>
  <p>Phone number 000.000.000</p>
  <p class="mail">mail@korva.com</p>
</div>
<div class="abs field" style="top:1787px">Your name</div>
<div class="abs field" style="top:1842px">E-mail Address</div>
<div class="abs field" style="top:1897px">Subject</div>
<div class="abs field message" style="top:1953px">Message</div>
<div class="abs submit">SUBMIT</div>

<!-- clients -->
<h2 class="abs section-title" style="top:2171px">Our Clients</h2>
<div class="abs clients">
  <div class="client"><span class="dot" style="background:#d22"></span>Brisa</div>
  <div class="client boxed">Palund</div>
  <div class="client">Tavel</div>
  <div class="client"><span class="dot" style="border-radius:50%"></span>Vexa</div>
  <div class="client">Orsk</div>
</div>

<footer class="abs site-footer">
  Home &nbsp;|&nbsp; Products &nbsp;|&nbsp; Solutions &nbsp;|&nbsp; Choose us &nbsp;|&nbsp; About us &nbsp;|&nbsp; Contact<br>
  Your info mail &nbsp;|&nbsp; Address &nbsp;|&nbsp; Phone number
</footer>

</body>
</html>
```